Super Stunning and Creative 1-page Infographic Needed

Take the attached content and covert it into a 1-page 8.5x11" stunning, and highly engaging infographic. The infographic must:

* Use Birch Supply colors
* Have icons and graphics used appropriately
* Look unique and creative, and super cool
* Be very eye catching

See attachment for content.

The topic is about retail inventory management. Retail = Store. Not warehouse looking. If you can add Birch Supply photos, this may enhance it. Just a consideration, but not necessary.

Target Market(s)

Birch Supply Store Owners

Industry/Entity Type

Retail Industry - Home Improvement

Font styles to use
Sans Serif

Requirements
Must have
• Birch Supply Colors, Super Creative, Stunning and Eye Capturing. Graphics and icons where they make sense.
Should not have
• Common infographic look. It must look different.

```html
<!DOCTYPE html>
<html lang="en">
<head>
<meta charset="utf-8">
<title>8 Misconceptions About Managing Your Inventory Debunked</title>
<link href="https://fonts.googleapis.com/css2?family=Montserrat:wght@300;400;500;600;700&display=swap" rel="stylesheet">
<style>
:root{
  --red:#d3122d;
  --red-dark:#a80d22;
  --ink:#1c1c1c;
  --body:#3a3a3a;
  --bg:#ececec;
  --white:#ffffff;
  --pink-soft:#f6c9cf;
  --pink-mid:#e98893;
  --gold:#f2b233;
}
*{margin:0;padding:0;box-sizing:border-box}
html,body{width:1200px;height:4710px;overflow:hidden}
body{font-family:"Montserrat",Arial,sans-serif;background:radial-gradient(circle at 30% 40%,#f4f4f4,var(--bg) 70%);position:relative;color:var(--ink)}
.header{position:absolute;left:0;top:0;width:1200px;height:330px;background:linear-gradient(120deg,var(--red) 0%,var(--red-dark) 100%)}
.header .big-eight{position:absolute;left:38px;top:40px;font-size:250px;font-weight:700;line-height:1;color:var(--white);letter-spacing:-6px;z-index:3}
.header .title{position:absolute;left:218px;top:92px;color:var(--white);line-height:1;z-index:3}
.title .light{display:block;font-weight:400;font-size:34px;letter-spacing:0;margin-bottom:4px}
.title .heavy{display:block;font-weight:700;font-size:68px;letter-spacing:-1.5px;line-height:0.98}
.art{position:absolute;border-radius:18px;z-index:1}
.art.truck{left:676px;top:0;width:524px;height:345px;border-radius:0;background:linear-gradient(160deg,#f4c531,#c9961a 55%,#3a3a3a)}
.path{position:absolute;left:0;top:0;z-index:0}
.item{position:absolute;z-index:2}
.item h2{font-size:28px;font-weight:500;line-height:1.24;color:var(--ink);letter-spacing:-0.4px}
.item h2 em{font-style:normal;color:var(--red);font-weight:600}
.item p{font-size:19.5px;font-weight:400;line-height:27px;color:var(--body);margin-top:14px;letter-spacing:-0.3px}
.item.right{text-align:right}
.num{position:absolute;font-size:165px;font-weight:600;color:var(--red);line-height:1;letter-spacing:-6px;z-index:2}
.art.pinkish{background:linear-gradient(150deg,var(--pink-soft),var(--pink-mid) 60%,var(--red))}
.art.warm{background:linear-gradient(150deg,#fbe2b0,var(--gold) 55%,var(--pink-mid))}
.footer{position:absolute;left:0;top:4470px;width:680px;height:240px;background:var(--red);color:var(--white);z-index:2}
.footer .f1{position:absolute;left:50px;top:34px;font-size:74px;font-weight:700;letter-spacing:-1px;line-height:1}
.footer .f2{position:absolute;left:50px;top:118px;font-size:44px;font-weight:300;line-height:1;display:flex;align-items:center;gap:16px;opacity:.85}
.footer .f2 .sq{width:38px;height:38px;background:rgba(255,255,255,.55)}
.footer .contact{position:absolute;left:50px;top:190px;font-size:20px;font-weight:500;display:flex;align-items:center;gap:10px}
.art.store{left:680px;top:4420px;width:520px;height:290px;border-radius:0;background:linear-gradient(180deg,#b9b2a7,#8a6b4f 55%,#5b5550)}
.store-name{position:absolute;left:820px;top:4470px;width:240px;text-align:center;font-size:34px;font-weight:700;color:var(--red);z-index:2}
</style>
</head>
<body>

<header class="header">
  <div class="big-eight">8</div>
  <h1 class="title">
    <span class="light">MISCONCEPTIONS</span>
    <span class="light">ABOUT MANAGINGYOUR</span>
    <span class="heavy">INVENTORY</span>
    <span class="heavy">DEBUNKED</span>
  </h1>
</header>
<div class="art truck" role="img" aria-label="Illustration of a yellow delivery truck with trailer"></div>

<svg class="path" width="1200" height="4710" aria-hidden="true">
  <polyline fill="none" stroke="#d3122d" stroke-width="2"
    points="604,330 604,357 955,357 955,864 178,864 178,1318 955,1318 955,1852 216,1852 216,2337 955,2337 955,2813 216,2813 216,3334 955,3334 955,3870 250,3870 250,4420"/>
</svg>

<section class="item" style="left:88px;top:392px;width:490px">
  <h2>Getting my <em>replenishment settings</em> right is the most important way to <em>manage inventory!</em></h2>
  <p>Maintaining strong inventory record accuracy (IRA) is the most critical factor toward staying in stock, addressing dead inventory, &amp; driving incremental profitability.</p>
</section>
<div class="num" style="left:372px;top:606px">01</div>
<div class="art pinkish" style="left:600px;top:360px;width:450px;height:440px" role="img" aria-label="Illustration of shelving, a search screen, a tablet checklist and a card terminal with coins"></div>

<section class="item right" style="left:555px;top:905px;width:548px">
  <h2>When <em>sales</em> have slowed,<br>inventory <em>needs cutting</em></h2>
  <p>Efforts to reduce inventory can be lethal, creating out of stocks, empty shelves, poor store image perception, and frustrated customers who will ultimately shop the competition. Instead, if inventories need to be reduced, prioritize by looking at unproductive products taking a more strategic approach to healthier inventory levels.</p>
</section>
<div class="art warm" style="left:25px;top:850px;width:460px;height:410px" role="img" aria-label="Illustration of a worker beside red shelving stocked with boxes"></div>
<div class="num" style="left:515px;top:1160px">02</div>

<section class="item" style="left:88px;top:1380px;width:530px">
  <h2><em>Dead stock</em> (stuff that hasn't sold in years) needs to be <em>marked down</em> and moved out</h2>
  <p>Leverage markdowns as a last resort. Instead, first check to see if the product is even physically in the store, priced competitively, redundant product in the set, or merchandised effectively. More times than not you can move product without having to sell it at a discount.</p>
</section>
<div class="num" style="left:292px;top:1635px">03</div>
<div class="art pinkish" style="left:640px;top:1350px;width:520px;height:470px" role="img" aria-label="Illustration of a worker moving boxes next to a large phone showing a checklist"></div>

<section class="item right" style="left:550px;top:1912px;width:553px">
  <h2>Working my <em>Ledgerline count sheets</em> will drive sustainable improvements to <em>IRA</em></h2>
  <p>Used to update and correct counts with no regard toward understanding what caused the issues, then this is a band-aid approach and typically won't provide much long-term IRA gain. Instead, work count sheets to understand the root of operational gaps and retrain staff as necessary for sustainable improvements.</p>
</section>
<div class="art warm" style="left:45px;top:1860px;width:440px;height:360px" role="img" aria-label="Illustration of a clipboard checklist beside shelves of boxes and a worker"></div>
<div class="num" style="left:515px;top:2165px">04</div>

<section class="item" style="left:88px;top:2380px;width:560px">
  <h2>Increasing my inventory depth will hurt <em>profits</em> &amp; drive down my <em>inventory turns</em></h2>
  <p>Stores who have deeper levels of inventory outperform stores that don't. When focused on raising inventory strategically through programs like economic order quantities, minimum order points, and preseason planner, inventory turns typically remain the same as inventory increases.</p>
</section>
<div class="num" style="left:472px;top:2635px">05</div>
<div class="art pinkish" style="left:680px;top:2420px;width:470px;height:380px" role="img" aria-label="Illustration of delivery trucks at a stockroom with shelving and a forklift"></div>

<section class="item right" style="left:565px;top:2870px;width:538px">
  <h2>Spending more than an hour (or more) working the <em>'RSO'</em> will result in better quality suggested orders</h2>
  <p>Typically, if it takes greater than 60 minutes to work your RSO each week per store, there are larger issues at play. The goal is to be able to review the RSO on an exception basis for outliers and transmit it through to then shift focus on other important store activities.</p>
</section>
<div class="art warm" style="left:60px;top:2840px;width:440px;height:380px" role="img" aria-label="Illustration of a laptop with stacked pallets, boxes, coins and small workers"></div>
<div class="num" style="left:718px;top:3150px">06</div>

<section class="item" style="left:88px;top:3385px;width:520px">
  <h2>Carry more weeks of <em>supply</em> on fast moving products and less on slower velocity <em>SKUs</em></h2>
  <p>Based on how Falcon Desk calculates order points, this can result in overstocking on faster goods and insufficient amounts of slower ones. Revisit your weeks of supply settings to ensure they are maintained at or near Birch Supply best practice levels.</p>
</section>
<div class="num" style="left:258px;top:3660px">07</div>
<div class="art pinkish" style="left:650px;top:3380px;width:490px;height:420px" role="img" aria-label="Illustration of a forklift, shelving and a scanner with workers"></div>

<section class="item right" style="left:615px;top:3948px;width:488px">
  <h2>The onset of <em>global supply chain</em> issues, reaching a <em>95% in-stock</em> position is next to impossible</h2>
  <p>Undoubtably, the industry supply problems make obtaining a higher in-stock position more challenging, but still quite probable. The key is to focus on what you are able to control within the four walls of your operations &amp; consistently execute the basics (i.e. count sheets, shooting the outs, item change management)</p>
</section>
<div class="art warm" style="left:75px;top:3950px;width:440px;height:380px" role="img" aria-label="Illustration of a delivery truck beside shelving stocked with yellow boxes and a worker"></div>
<div class="num" style="left:508px;top:4268px">08</div>

<div class="art store" role="img" aria-label="Photo of a hardware store front with outdoor displays"></div>
<div class="store-name">Birch Supply</div>

<footer class="footer">
  <div class="f1">Inventory</div>
  <div class="f2"><span class="sq"></span>Management</div>
  <div class="contact">
    <svg width="18" height="18" viewBox="0 0 24 24" aria-hidden="true"><path fill="#fff" d="M6.6 10.8a15 15 0 0 0 6.6 6.6l2.2-2.2c.3-.3.7-.4 1-.2 1.1.4 2.3.6 3.6.6.6 0 1 .4 1 1V20c0 .6-.4 1-1 1A17 17 0 0 1 3 4c0-.6.4-1 1-1h3.5c.6 0 1 .4 1 1 0 1.3.2 2.5.6 3.6.1.3 0 .7-.2 1z"/></svg>
    <span>555.014.2290</span><span>|</span>
    <svg width="18" height="18" viewBox="0 0 24 24" aria-hidden="true"><path fill="#fff" d="M2 5h20v14H2zm2 2v.5l8 5 8-5V7l-8 5z"/></svg>
    <span>StoreOperations@birchsupply.com</span>
  </div>
</footer>

</body>
</html>
```